holloway paving service

Needs to have phone number 0418259730 and email markholloway@brightmail.com.au.
ABN 62318470915
name mark holloway

For all your concreting solutions
Excavation
Exposed & colour concrete
House & shed slabs
Driveways
Landing & steps

Contact Information for Business Card

ph 0418259730
email markholloway@brightmail.com.au.
ABN 62318470915
name mark holloway

```html
<!DOCTYPE html>
<html lang="en">
<head>
<meta charset="utf-8">
<title>Holloway Paving Service — Business Card</title>
<link rel="stylesheet" href="https://fonts.googleapis.com/css2?family=Roboto:wght@400;500&family=Roboto+Condensed:wght@400;700&display=swap">
<style>
  :root {
    --backdrop: #e9e6e1;
    --paper: #ffffff;
    --orange: #ec6a20;
    --slate: #606061;
    --slate-text: #555555;
    --rule: #8a8a8a;
  }
  * { box-sizing: border-box; margin: 0; padding: 0; }
  html, body { width: 1200px; height: 886px; overflow: hidden; }
  body {
    background: var(--backdrop);
    font-family: "Roboto", sans-serif;
    position: relative;
  }
  .card {
    position: absolute;
    width: 540px;
    height: 310px;
    background: var(--paper);
    box-shadow: 0 6px 18px rgba(0,0,0,.18);
    overflow: hidden;
  }
  .card--front { left: 50px; top: 288px; }
  .card--back  { left: 610px; top: 288px; }

  .card__art { position: absolute; inset: 0; width: 540px; height: 310px; }

  .wordmark {
    position: absolute;
    font-family: "Roboto Condensed", sans-serif;
    text-align: center;
    line-height: 1.15;
  }
  .wordmark__name {
    color: var(--orange);
    font-weight: 700;
    font-size: 21px;
    letter-spacing: .3px;
    text-transform: uppercase;
    white-space: nowrap;
  }
  .wordmark__rule {
    display: flex; align-items: center; justify-content: center;
    margin: 3px 0;
  }
  .wordmark__rule::before {
    content: ""; width: 150px; height: 1.5px; background: var(--rule);
  }
  .wordmark__phone {
    color: var(--orange);
    font-size: 18px;
    letter-spacing: 1.5px;
  }

  .card--front .wordmark { left: 20px; top: 34px; width: 250px; }

  .brand-plate {
    position: absolute;
    display: flex; align-items: center; gap: 8px;
    font-family: "Roboto Condensed", sans-serif;
    font-weight: 700;
    text-transform: uppercase;
    color: var(--paper);
    white-space: nowrap;
  }
  .brand-plate__square { width: 14px; height: 14px; background: var(--paper); }
  .card--front .brand-plate { right: 34px; top: 36px; font-size: 24px; }

  .contact {
    position: absolute; left: 240px; bottom: 20px;
    color: var(--paper);
    font-size: 14px; line-height: 1.5;
  }
  .contact__name {
    font-family: "Roboto Condensed", sans-serif;
    font-weight: 700; font-size: 22px;
    text-transform: uppercase; margin-bottom: 2px;
  }
  .contact__row { display: flex; align-items: center; gap: 8px; white-space: nowrap; }
  .contact__row svg { width: 12px; height: 12px; flex: none; }
  .contact__row--plain { padding-left: 20px; }

  .card--back .brand-plate {
    left: 300px; top: 46px; font-size: 20px; color: var(--slate);
  }
  .card--back .brand-plate__square { background: var(--orange); }
  .divider {
    position: absolute; left: 290px; top: 90px; width: 210px; height: 2px;
    background: var(--orange);
  }
  .card--back .wordmark { left: 265px; top: 106px; width: 260px; }

  .services {
    position: absolute; left: 36px; top: 48px;
    list-style: none;
    color: var(--slate-text);
    font-size: 15px; line-height: 1.75;
  }
  .services__lead { color: var(--slate); font-weight: 500; margin-bottom: 4px; }
</style>
</head>
<body>

<section class="card card--front" aria-label="Business card front">
  <svg class="card__art" viewBox="0 0 540 310" aria-hidden="true">
    <polygon points="140,310 330,0 540,0 540,310" fill="var(--orange)"/>
    <polygon points="330,0 540,0 540,80 238,150" fill="var(--slate)"/>
  </svg>

  <div class="wordmark">
    <div class="wordmark__name">Holloway Paving Service</div>
    <div class="wordmark__rule"></div>
    <div class="wordmark__phone">0418259730</div>
  </div>

  <div class="brand-plate">
    <span class="brand-plate__square"></span>Holloway
  </div>

  <div class="contact">
    <div class="contact__name">Mark Holloway</div>
    <div class="contact__row">
      <svg viewBox="0 0 12 12"><path d="M2.5 1 L4.5 1 L5.3 3.6 L4 4.6 Q5 7 7.4 8 L8.4 6.7 L11 7.5 L11 9.5 Q11 11 9.5 11 Q1 10 1 2.5 Q1 1 2.5 1 Z" fill="currentColor"/></svg>
      0418259730
    </div>
    <div class="contact__row">
      <svg viewBox="0 0 12 12"><rect x="1" y="2.5" width="10" height="7" fill="currentColor"/><path d="M1 2.5 L6 6.5 L11 2.5" stroke="var(--orange)" fill="none"/></svg>
      markholloway@brightmail.com.au
    </div>
    <div class="contact__row">
      <svg viewBox="0 0 12 12"><circle cx="6" cy="6" r="5" fill="currentColor"/></svg>
      www.hollowaypaving.com.au
    </div>
    <div class="contact__row contact__row--plain">ABN 62318470915</div>
  </div>
</section>

<section class="card card--back" aria-label="Business card back">
  <ul class="services">
    <li class="services__lead">For all your concreting solutions</li>
    <li>Excavation</li>
    <li>Exposed &amp; colour concrete</li>
    <li>House &amp; shed slabs</li>
    <li>Driveways</li>
    <li>Landing &amp; steps</li>
  </ul>

  <div class="brand-plate">
    <span class="brand-plate__square"></span>Holloway
  </div>
  <div class="divider"></div>

  <div class="wordmark">
    <div class="wordmark__name">Holloway Paving Service</div>
    <div class="wordmark__rule"></div>
    <div class="wordmark__phone">0418259730</div>
  </div>
</section>

</body>
</html>
```